Nitrogen generation business website

Project Overview:
This project aims to create a sleek, user-friendly, and responsive WordPress template for Flo7K3, a provider of Nitrogen generation solutions. The site will serve as a primary touchpoint for customers and businesses looking to enquire about or purchase Flo7K3 products and services. The website should clearly communicate the benefits of working with Flo7K3 as a distributor, focusing on ease of access, expert consultation, and fast, reliable service.
Target Audience:
• Industrial companies seeking Nitrogen solutions.
• Engineers, facility managers, and purchasing teams in need of high-quality Nitrogen systems.
• Partners or businesses seeking to collaborate or purchase through a distributor.
Key Objectives:
1. Establish Flo7K3’s Brand Identity: Use the bold, energetic logo and branding of Flo7K3 (as seen in the uploaded logo) throughout the design. Ensure the brand’s personality shines, with a focus on modernity, reliability, and innovation.
2. Showcase Products and Solutions: Display detailed product categories and descriptions, emphasising the solutions Flo7K3 offers.
3. Lead Generation: Incorporate contact forms, quote requests, and easy-to-find CTAs to convert visitors into leads.
4. User-Centric Design: The design must be intuitive and user-friendly, providing a smooth experience across desktop and mobile devices.
Design Requirements:
1. Home Page:
• Hero Banner: A dynamic, visually engaging hero banner featuring air and gas purification systems, paired with strong CTAs like “Request a Quote” or “Contact Us for Solutions.” The banner should align with the vibrant red and yellow tones in the Flo7K3 logo.
• Key Product Categories: Introduce the main product categories with icons or images linked to individual product pages.
• Flo7K3 Expertise Section: A section emphasising the company’s role as a trusted distributor, backed by experience and a strong partnership network.
• Why Choose Flo7K3: Highlight 3-4 major benefits, such as “Quick Delivery,” “Expert Consultation,” and “Innovative Technology.”
• Client Testimonials/Partners: Space for customer feedback, testimonials, or logos of partner companies to build trust.
• Newsletter or Enquiry Form: Place a compact form for capturing visitor details for quotes, enquiries, or subscriptions.
2. Product Pages:
• Category Pages: Create well-structured product category pages (e.g., Air Filtration Systems, Nitrogen Generators) similar to industry-standard designs. Each category page should feature professional imagery, short product descriptions, and links to detail pages.
• Product Detail Pages: Each product page will contain:
• High-quality images of the product.
• Detailed specifications, technical descriptions, and features.
• Options to download datasheets or brochures (PDF format).
• Clear CTAs to request a quote or contact sales.
• Product Comparison Tool (Optional): Allow users to compare multiple products, emphasising key features and specifications.
3. About Flo7K3 Page:
• Provide an overview of Flo7K3’s history, mission, and the value it provides as a leading distributor.
• Highlight industry expertise, the partnership network, and any accolades or certifications.
• Mention any regional advantages or special services (e.g., fast delivery times, on-site consultation).
4. Contact Us Page:
• Clean and Simple Form: Include fields for general inquiries or specific product requests.
• Contact Information: Display the company’s, email address info@flo7k3.co.uk.
5. Additional Functionalities:
• Responsive Design: Ensure the design is fully responsive, optimised for mobile, tablet, and desktop viewing.
• SEO Optimisation: Include best practices for search engine optimization (SEO), including clean URLs, meta tags, and image alt text.
• Fast Loading Speed: Optimise images, scripts, and code for fast loading times to improve user experience.
• Social Media Integration: Provide links to social media profiles (if applicable) and potentially include a feed for recent updates.
• Optional Blog: Create a blog space for sharing industry news, product updates, or educational content to engage with visitors and improve SEO.
Style Guide:
1. Color Palette:
• Use colors consistent with the Flo7K3 logo: Red (#FF0000) and Yellow (#FFD700) as primary colors. Incorporate neutral colors (such as white, gray, or black) for balance and readability.
• Accent colors may be introduced for subtle highlights, but the focus should be on the bold, energetic color scheme of Flo7K3.
2. Typography:
• Primary Font for Headings: A bold, modern sans-serif font that complements the strong branding of Flo7K3.
• Secondary Font for Body Text: Clean, easy-to-read sans-serif or serif font for optimal readability across devices.
• Typography Emphasis: Use large, bold typography for headlines to match the boldness of the logo and brand identity.
3. Imagery:
• Use high-quality industrial and technical imagery that reflects the air and gas purification products Flo7K3 distributes.
• Incorporate imagery showing products in action, e.g., in industrial settings or installations.
• Avoid clutter; ensure images are used to enhance user understanding, not overwhelm.
4. Icons:
• Utilise modern, flat-style icons that align with the clean and professional image of Flo7K3. Icons could represent services such as “Fast Delivery,” “Expert Support,” and “High-Quality Products.”
Functionality Requirements:
1. Content Management System (CMS): Build the site using WordPress for easy content management, allowing Flo7K3 staff to update content, product information, and blog posts.
2. Quote Request Integration: Ensure the site has a functional and easy-to-access “Request a Quote” form that appears on every product and service page.
3. Customer Support Section: Optionally include a section for FAQs, product guides, or a knowledge base to support customers and prospects.
4. Security: Implement SSL encryption and ensure that other security best practices (e.g., spam prevention for forms) are followed.
5. Multilingual Support (Optional): Provide the option to support multiple languages, depending on the regional scope of Flo7K3’s distribution services.
Deliverables:
• WordPress template with a homepage, product pages, about section, and contact page.
• SEO-friendly and responsive design.
• Clear CTAs for lead generation (e.g., “Request a Quote”).
• User-friendly interface for both desktop and mobile devices.
Inspiration/Competitors:
• Competitor Analysis: Research similar distributors in the air and gas purification industry for design inspiration.
• Brand Consistency: Ensure Flo7K3’s bold branding is prominent and differentiates it from competitors.
Target Market(s)
Food & Beverage manufacturers, Laser Cutting, Electronics manufacturers, General Industrial Manufacturers

```html
<!DOCTYPE html>
<html lang="en">
<head>
<meta charset="utf-8">
<title>Flo7K3 – Nitrogen Generation Solutions</title>
<link href="https://fonts.googleapis.com/css2?family=Montserrat:wght@500;600;700;800&family=Lato:wght@400;700&display=swap" rel="stylesheet">
<style>
:root{
  --red:#e8141c;
  --orange:#f26a14;
  --yellow:#f4b21b;
  --gold:#e9a800;
  --cream:#fdf8ee;
  --grey-bg:#f3f3f3;
  --ink:#1c1c1c;
  --muted:#444;
  --footer:#121212;
  --btn:linear-gradient(180deg,var(--red) 0%,var(--orange) 55%,var(--yellow) 100%);
}
*{box-sizing:border-box;margin:0;padding:0}
html,body{width:1200px;height:4577px;overflow:hidden}
body{font-family:"Lato",sans-serif;color:var(--ink);background:#fff;position:relative}
.btn{position:absolute;display:flex;align-items:center;justify-content:center;font-family:"Montserrat",sans-serif;font-weight:700;font-size:15px;color:#222;background:var(--btn);border-radius:24px 4px 24px 4px;text-transform:uppercase}
.btn.dark{color:#3a0b00}
.dots{position:absolute;left:50%;transform:translateX(-50%);width:26px;height:14px}
.dots::before,.dots::after{content:"";position:absolute;border-radius:50%}
.dots::before{width:13px;height:13px;left:0;top:2px;background:var(--yellow)}
.dots::after{width:9px;height:9px;left:18px;top:0;background:var(--yellow)}
.dots.white::before,.dots.white::after{background:#fff}
.title{position:absolute;left:0;right:0;text-align:center;font-family:"Montserrat",sans-serif;font-weight:800;font-size:40px;text-transform:uppercase;color:var(--red)}
.title span{color:var(--yellow)}

/* top bar */
.topbar{position:absolute;top:0;left:0;width:1200px;height:115px;background:#fff}
.brand{position:absolute;left:112px;top:20px;font-family:"Montserrat",sans-serif;font-weight:800;font-size:40px;color:var(--red)}
.contact-line{position:absolute;top:28px;left:370px;font-size:16px;color:#333;display:flex;gap:26px;align-items:center}
.contact-line .sep{width:1px;height:22px;background:#555}
.contact-line svg{width:14px;height:14px;vertical-align:-2px;margin-right:6px}
.top-cta{left:838px;top:21px;width:250px;height:38px;font-size:13px;color:#fff;border-radius:10px;background:linear-gradient(90deg,var(--red),var(--orange) 60%,var(--yellow))}
.nav{position:absolute;left:110px;top:80px;width:978px;height:62px;background:var(--red);border-radius:10px;display:flex;align-items:center;z-index:2}
.nav a{font-family:"Montserrat",sans-serif;font-weight:600;font-size:14px;color:#fff;text-decoration:none;position:absolute}
.nav a.active{border-bottom:2px solid #fff;padding-bottom:2px}
.nav .search{position:absolute;right:22px;width:26px;height:26px;border-radius:50%;background:#fff;display:flex;align-items:center;justify-content:center}

/* hero */
.hero{position:absolute;top:115px;left:0;width:1200px;height:562px}
.hero-img{position:absolute;inset:0;background:linear-gradient(100deg,#0c2a44 0%,#12395e 35%,#2c5f8f 55%,#7f6a40 72%,#1e3f66 100%)}
.hero-shade{position:absolute;inset:0;background:linear-gradient(90deg,rgba(5,18,35,.85),rgba(5,18,35,0) 55%)}
.hero h3{position:absolute;left:112px;top:140px;font-family:"Montserrat",sans-serif;font-weight:700;font-size:27px;color:#fff}
.hero h1{position:absolute;left:108px;top:170px;font-family:"Montserrat",sans-serif;font-weight:800;font-size:100px;color:#fff;letter-spacing:1px}
.hero p{position:absolute;left:112px;top:290px;width:360px;font-size:15px;line-height:27px;color:#fff}
.hero .btn{left:110px;top:392px;width:203px;height:48px}

/* about */
.about{position:absolute;top:677px;left:0;width:1200px;height:461px}
.about .dots{top:60px}
.about .title{top:86px}
.about p{position:absolute;left:180px;width:840px;text-align:center;font-size:15px;line-height:30px;color:#222}
.about .btn{left:498px;top:336px;width:169px;height:52px}

/* why */
.why{position:absolute;top:1138px;left:0;width:1200px;height:480px;background:var(--cream)}
.why .dots{top:76px}
.why .title{top:100px}
.feature{position:absolute;top:183px;width:300px;text-align:center}
.ring{width:165px;height:165px;border-radius:50%;background:var(--yellow);margin:0 auto;display:flex;align-items:center;justify-content:center;box-shadow:0 6px 14px rgba(0,0,0,.12)}
.ring div{width:139px;height:139px;border-radius:50%;background:#fff;display:flex;align-items:center;justify-content:center}
.feature h4{font-family:"Montserrat",sans-serif;font-weight:600;font-size:19px;margin-top:20px;color:#111}

/* products */
.products{position:absolute;top:1618px;left:0;width:1200px;height:700px}
.products .dots{top:70px}
.products .title{top:92px;color:#fff}
.card{position:absolute;top:176px;width:329px;height:434px;background:#fff;border:1px solid #ccc;border-radius:18px;box-shadow:0 4px 12px rgba(0,0,0,.08)}
.card.featured{border-color:var(--red);box-shadow:0 6px 18px rgba(232,20,28,.2)}
.card .pic{position:absolute;left:14px;top:18px;right:14px;height:350px;border-radius:16px}
.card.featured .pic{height:290px;border:1px solid #999}
.card h5{position:absolute;left:0;right:0;top:385px;text-align:center;font-family:"Montserrat",sans-serif;font-weight:700;font-size:18px}
.card.featured h5{top:326px}
.card small{position:absolute;left:30px;right:30px;top:360px;text-align:center;font-size:13px;line-height:26px;color:#333}
.products .btn{left:516px;top:684px;width:168px;height:50px}

/* testimonials */
.testi{position:absolute;top:2380px;left:0;width:1200px;height:642px}
.testi .dots{top:48px}
.testi .title{top:72px}
.avatar{position:absolute;border-radius:50%}
.testi .name{position:absolute;top:319px;left:0;right:0;text-align:center;font-family:"Montserrat",sans-serif;font-weight:600;font-size:20px;padding-left:10px}
.testi .place{position:absolute;top:354px;left:0;right:0;text-align:center;font-family:"Montserrat",sans-serif;font-size:12px;color:#777;padding-left:10px}
.testi .stars{position:absolute;top:370px;left:0;right:0;text-align:center;font-size:30px;color:var(--yellow);letter-spacing:1px;padding-left:10px}
.testi blockquote{position:absolute;top:425px;left:280px;width:660px;text-align:center;font-family:"Montserrat",sans-serif;font-weight:500;font-size:15px;line-height:26px;color:#222}
.quote{position:absolute;font-family:Georgia,serif;font-size:220px;color:#ddd;line-height:1}
.pager{position:absolute;top:533px;left:540px;display:flex;gap:8px}
.pager i{width:12px;height:12px;border-radius:50%;background:#dfe1ea;display:block}
.pager i.on{background:var(--yellow)}
.spark{position:absolute;border-radius:50%}

/* services */
.services{position:absolute;top:3022px;left:0;width:1200px;height:551px;background:var(--grey-bg)}
.services .dots{top:64px}
.services .title{top:84px}
.svc{position:absolute;top:160px;width:300px;height:359px;border-radius:14px;overflow:hidden}
.svc .shade{position:absolute;inset:0;background:linear-gradient(180deg,rgba(0,0,0,0) 60%,rgba(0,0,0,.75))}
.svc span{position:absolute;left:28px;bottom:18px;font-family:"Montserrat",sans-serif;font-weight:700;font-size:17px;color:#fff}
.svc svg{position:absolute;right:28px;bottom:20px}

/* contact */
.contact{position:absolute;top:3573px;left:0;width:1200px;height:566px}
.contact .dots{top:64px}
.contact .title{top:84px}
.info{position:absolute;left:110px;display:flex;gap:12px}
.info .ic{width:62px;height:62px;border-radius:50%;background:var(--yellow);display:flex;align-items:center;justify-content:center;flex:none}
.info h6{font-family:"Montserrat",sans-serif;font-weight:700;font-size:16px;margin-top:6px}
.info p{font-size:15px;margin-top:4px}
.field{position:absolute;background:#fff;box-shadow:0 2px 8px rgba(0,0,0,.12);font-size:14px;color:#555;padding:16px 18px}
.contact .btn{left:507px;top:432px;width:169px;height:52px;color:#4a0d00}

/* footer */
.footer{position:absolute;top:4139px;left:0;width:1200px;height:438px;background:var(--footer);color:#fff}
.footer .brand{left:112px;top:100px;font-size:46px}
.fcol{position:absolute;top:94px}
.fcol h6{font-family:"Montserrat",sans-serif;font-weight:500;font-size:21px;letter-spacing:.5px;margin-bottom:14px}
.fcol li{list-style:none;font-size:15px;line-height:35px;padding-left:6px}
.news-input{position:absolute;left:795px;top:124px;width:293px;height:44px;background:#fff;border-radius:8px;color:#888;font-size:13px;padding:14px 18px}
.footer .btn{left:793px;top:195px;width:167px;height:50px;color:#3a0b00;font-size:15px}
.social{position:absolute;left:112px;top:213px;display:flex;gap:19px}
.social i{width:26px;height:26px;border-radius:50%;border:1.5px solid #fff;display:block}
.social i.on{background:var(--yellow);border-color:var(--yellow)}
.footer hr{position:absolute;left:110px;top:347px;width:978px;border:0;border-top:1.5px solid #777}
.copy{position:absolute;top:384px;left:0;right:0;text-align:center;font-family:"Montserrat",sans-serif;font-weight:600;font-size:14px}
</style>
</head>
<body>

<header class="topbar">
  <div class="brand">Flo7K3</div>
  <div class="contact-line">
    <span><svg viewBox="0 0 24 24"><path fill="#333" d="M6.6 10.8a15.1 15.1 0 006.6 6.6l2.2-2.2c.3-.3.7-.4 1-.2 1.1.4 2.3.6 3.6.6.6 0 1 .4 1 1V20c0 .6-.4 1-1 1A17 17 0 013 4c0-.6.4-1 1-1h3.5c.6 0 1 .4 1 1 0 1.3.2 2.5.6 3.6.1.3 0 .7-.2 1z"/></svg>+1 555 014 2290</span>
    <span class="sep"></span>
    <span><svg viewBox="0 0 24 24"><path fill="#333" d="M2 5h20v14H2z"/><path fill="#fff" d="M3 6l9 6 9-6v1l-9 6-9-6z"/></svg>info@flo7k3.co.uk</span>
    <span class="sep"></span>
  </div>
  <div class="btn top-cta">Contact us for solutions</div>
</header>

<nav class="nav">
  <a class="active" style="left:40px">HOME</a>
  <a style="left:164px">ABOUT</a>
  <a style="left:298px">PRODUCT</a>
  <a style="left:448px">SERVICES</a>
  <a style="left:600px">INDUSTRIES</a>
  <a style="left:770px">CONTACT US</a>
  <span class="search"><svg width="12" height="12" viewBox="0 0 24 24"><circle cx="10" cy="10" r="6" fill="none" stroke="#333" stroke-width="3"/><path d="M15 15l6 6" stroke="#333" stroke-width="3"/></svg></span>
</nav>

<section class="hero">
  <div class="hero-img" role="img" aria-label="Industrial gas plant with towers and pipework lit at night"></div>
  <div class="hero-shade"></div>
  <h3>WELCOME TO</h3>
  <h1>FLO7K3</h1>
  <p>Lorem ipsum dolor sit amet, consectetur adipiscing elit, sed do eiusmod tempor incididunt ut labore et dolore magna aliqua.</p>
  <div class="btn dark">Request a quote</div>
</section>

<section class="about">
  <span class="dots"></span>
  <h2 class="title">About <span>Flo7K3</span></h2>
  <p style="top:155px">Flo7K3 specialises in supplying, installing, and servicing nitrogen generators for efficient on-site nitrogen production. Enhance your operations with our reliable, cost-effective nitrogen solutions. Discover how our advanced nitrogen generators can optimise your business today.</p>
  <p style="top:273px">Contact Flo7K3 for expert nitrogen generation services.</p>
  <div class="btn dark">Get started</div>
</section>

<section class="why">
  <span class="dots"></span>
  <h2 class="title">Why <span>choose us</span></h2>
  <div class="feature" style="left:108px">
    <div class="ring"><div><svg width="64" height="64" viewBox="0 0 64 64" fill="none" stroke="#f26a14" stroke-width="2.5"><rect x="6" y="28" width="32" height="20"/><path d="M38 34h11l8 8v6H38z"/><circle cx="16" cy="50" r="5"/><circle cx="48" cy="50" r="5"/><circle cx="36" cy="14" r="9"/><path d="M36 9v5l4 2"/></svg></div></div>
    <h4>Quick Delivery</h4>
  </div>
  <div class="feature" style="left:437px">
    <div class="ring"><div><svg width="64" height="64" viewBox="0 0 64 64" fill="none" stroke="#f26a14" stroke-width="2.5"><circle cx="32" cy="16" r="8"/><path d="M28 26h8M29 30h6"/><circle cx="14" cy="36" r="5"/><circle cx="50" cy="36" r="5"/><path d="M4 56c0-8 4-12 10-12s10 4 10 12M40 56c0-8 4-12 10-12s10 4 10 12M20 50h24"/></svg></div></div>
    <h4>Expert Consultation</h4>
  </div>
  <div class="feature" style="left:766px">
    <div class="ring"><div><svg width="64" height="64" viewBox="0 0 64 64" fill="none" stroke="#f26a14" stroke-width="2.5"><circle cx="32" cy="30" r="12"/><circle cx="32" cy="30" r="20" stroke-dasharray="6 5"/><path d="M28 44v8h8v-8M32 24v8"/></svg></div></div>
    <h4>Innovative Technology</h4>
  </div>
</section>

<section class="products">
  <svg width="1200" height="540" style="position:absolute;left:0;top:0"><path d="M0 0H1200V305Q1100 330 1040 375H160Q100 330 0 305Z" fill="#e9a800"/></svg>
  <span class="dots white"></span>
  <h2 class="title">Our product</h2>
  <div class="card" style="left:71px">
    <div class="pic" role="img" aria-label="Row of compressed air filter housings and cartridges" style="background:linear-gradient(180deg,#ececec,#dadada)"></div>
    <h5>AIR FILTERATION</h5>
  </div>
  <div class="card featured" style="left:437px">
    <div class="pic" role="img" aria-label="Twin-tower nitrogen generator skid" style="background:linear-gradient(180deg,#eee,#d6d6d6)"></div>
    <h5>NITROGEN GENERATOR</h5>
    <small>Excepteur sint occaecat cupidatat non proident, sunt in culpa</small>
  </div>
  <div class="card" style="left:802px">
    <div class="pic" role="img" aria-label="Modular air dryer pre-treatment units" style="background:linear-gradient(180deg,#ececec,#dadada)"></div>
    <h5>PRE-TREATMENT</h5>
  </div>
  <div class="btn dark">View more</div>
</section>

<section class="testi">
  <span class="dots"></span>
  <h2 class="title">What our <span>customer says</span></h2>
  <div class="avatar" role="img" aria-label="Customer portrait" style="left:542px;top:160px;width:136px;height:136px;background:linear-gradient(180deg,#f2d7b6,#c99570)"></div>
  <div class="avatar" role="img" aria-label="Customer portrait" style="left:138px;top:235px;width:66px;height:66px;background:linear-gradient(180deg,#e9c7a8,#b98a6a)"></div>
  <div class="avatar" role="img" aria-label="Customer portrait" style="left:1015px;top:162px;width:46px;height:46px;background:linear-gradient(180deg,#d9c0aa,#8a6a55)"></div>
  <span class="spark" style="left:383px;top:276px;width:12px;height:12px;background:var(--red)"></span>
  <span class="spark" style="left:898px;top:237px;width:6px;height:6px;background:var(--yellow)"></span>
  <div class="quote" style="left:165px;top:305px">“</div>
  <div class="quote" style="left:955px;top:408px">”</div>
  <div class="name">Marcus Elwood</div>
  <div class="place">United States</div>
  <div class="stars">★★★★★</div>
  <blockquote>Itaque earum rerum hic tenetur a sapiente delectus, ut aut reiciendis voluptatibus maiores alias. Consequatur aut perferendis doloribus asperiores repellat.Et harum quidem rerum facilis est et expedita distinctio.</blockquote>
  <div class="pager"><i></i><i></i><i></i><i class="on"></i><i></i><i></i></div>
</section>

<section class="services">
  <span class="dots"></span>
  <h2 class="title">Our <span>services</span></h2>
  <div class="svc" style="left:112px"><div role="img" aria-label="Engineers reviewing plans in a factory" style="position:absolute;inset:0;background:linear-gradient(160deg,#5d7a9c,#26384f)"></div><div class="shade"></div><span>CONSULTATION</span><svg width="16" height="16" viewBox="0 0 16 16"><circle cx="8" cy="8" r="8" fill="#fff"/><path d="M5 8h6M8 5l3 3-3 3" stroke="#222" stroke-width="1.8" fill="none"/></svg></div>
  <div class="svc" style="left:450px"><div role="img" aria-label="Industrial plant at dusk" style="position:absolute;inset:0;background:linear-gradient(180deg,#b8b0c8,#7d6b6a 55%,#2a2a30)"></div><div class="shade"></div><span>INSTALLATION</span><svg width="16" height="16" viewBox="0 0 16 16"><circle cx="8" cy="8" r="8" fill="#fff"/><path d="M5 8h6M8 5l3 3-3 3" stroke="#222" stroke-width="1.8" fill="none"/></svg></div>
  <div class="svc" style="left:788px"><div role="img" aria-label="Technician in hard hat inspecting equipment" style="position:absolute;inset:0;background:linear-gradient(160deg,#8a6e4e,#4a3a2c 60%,#2a231d)"></div><div class="shade"></div><span>MAINTENANCE</span><svg width="16" height="16" viewBox="0 0 16 16"><circle cx="8" cy="8" r="8" fill="#fff"/><path d="M5 8h6M8 5l3 3-3 3" stroke="#222" stroke-width="1.8" fill="none"/></svg></div>
</section>

<section class="contact">
  <span class="dots"></span>
  <h2 class="title">Get in <span>touch with us</span></h2>
  <div class="info" style="top:172px"><span class="ic"><svg width="22" height="26" viewBox="0 0 24 28"><path fill="#fff" d="M12 0a10 10 0 0110 10c0 8-10 18-10 18S2 18 2 10A10 10 0 0112 0z"/><circle cx="12" cy="10" r="4" fill="#f4b21b"/></svg></span><div><h6>LOCATION</h6><p>Flo7K3, United States</p></div></div>
  <div class="info" style="top:298px"><span class="ic"><svg width="24" height="24" viewBox="0 0 24 24"><path fill="#fff" d="M6.6 10.8a15.1 15.1 0 006.6 6.6l2.2-2.2c.3-.3.7-.4 1-.2 1.1.4 2.3.6 3.6.6.6 0 1 .4 1 1V20c0 .6-.4 1-1 1A17 17 0 013 4c0-.6.4-1 1-1h3.5c.6 0 1 .4 1 1 0 1.3.2 2.5.6 3.6.1.3 0 .7-.2 1z"/></svg></span><div><h6>PHONE NUMBER</h6><p>+1 555 014 2290</p></div></div>
  <div class="info" style="top:412px"><span class="ic"><svg width="24" height="20" viewBox="0 0 24 20"><rect width="24" height="20" rx="2" fill="#fff"/><path d="M2 3l10 7 10-7" stroke="#f4b21b" stroke-width="2" fill="none"/></svg></span><div><h6>EMAIL ADDRESS</h6><p>info@flo7k3.co.uk</p></div></div>
  <div class="field" style="left:507px;top:164px;width:283px;height:48px">First Name</div>
  <div class="field" style="left:801px;top:164px;width:283px;height:48px">Your Email</div>
  <div class="field" style="left:507px;top:226px;width:283px;height:48px">Your Phone</div>
  <div class="field" style="left:801px;top:226px;width:283px;height:48px">Service<svg width="10" height="6" viewBox="0 0 10 6" style="position:absolute;right:14px;top:21px"><path d="M0 0h10L5 6z" fill="#222"/></svg></div>
  <div class="field" style="left:507px;top:294px;width:577px;height:106px">Message</div>
  <div class="btn">Submit</div>
</section>

<footer class="footer">
  <div class="brand">Flo7K3</div>
  <div class="social"><i class="on"></i><i></i><i></i><i></i></div>
  <div class="fcol" style="left:387px"><h6>QUICK LINKS</h6><ul><li>Home</li><li>Products</li><li>Services</li><li>Industries</li><li>Contact Us</li></ul></div>
  <div class="fcol" style="left:593px"><h6>HELP LINKS</h6><ul><li>FAQ</li><li>Terms of use</li><li>Privacy Policy</li><li>Support Links</li><li>Conditions</li></ul></div>
  <div class="fcol" style="left:795px"><h6>NEWSLETTER</h6></div>
  <div class="news-input">Enter The Email</div>
  <div class="btn">Subscribe us</div>
  <hr>
  <div class="copy">Copyrights@2024.Flo7K3.All Rights Reserved</div>
</footer>

</body>
</html>
```